Keystone Trench Co Business Card*

Looking for a professional, clean and crisp business card

I am in the underground utilities industry and am just looking for a really impressive business card. I would like our card to be white with our symbol crisp and clear with it protruding. I also have a business partner that will require his name and info on the card once the design is set. I would like to have our website info on the card which is;
http://keystonetrenchco.example/

Contact Information for Business Card

Website, contact name, number and email

```html
<!DOCTYPE html>
<html lang="en">
<head>
<meta charset="utf-8">
<title>Keystone Trench Co — Business Card</title>
<link rel="stylesheet" href="https://fonts.googleapis.com/css2?family=Oswald:wght@500;600&family=Poppins:wght@400&display=swap">
<style>
  :root {
    --page: #e9e7e3;
    --card-white: #ffffff;
    --ink: #050608;
    --band: #3a4049;
    --navy: #2c3440;
    --text: #2b2f36;
    --accent: #2f4f9e;
    --ghost: #1b1d21;
  }
  * { margin: 0; padding: 0; box-sizing: border-box; }
  html, body { width: 1200px; height: 859px; overflow: hidden; background: var(--page); }
  .canvas { position: relative; width: 1200px; height: 859px; }
  .card {
    position: absolute; top: 288px; width: 501px; height: 285px;
    background: var(--card-white); overflow: hidden;
    box-shadow: 0 6px 14px rgba(0,0,0,0.25);
  }
  .card--front { left: 59px; }
  .card--back { left: 639px; }
  .card-shapes { position: absolute; inset: 0; width: 100%; height: 100%; }
  .brand-name {
    position: absolute; font-family: "Oswald", sans-serif; font-weight: 600;
    text-transform: uppercase; text-align: center; line-height: 1.0; letter-spacing: 1px;
  }
  .card--front .brand-name { left: 352px; top: 46px; width: 140px; font-size: 24px; color: var(--card-white); }
  .card--back .brand-name--mark { left: 14px; top: 50px; width: 136px; font-size: 24px; color: var(--ink); }
  .card--back .brand-name--ghost { left: 262px; top: 92px; width: 224px; font-size: 44px; color: var(--ghost); }
  .contact-name {
    position: absolute; left: 18px; top: 150px;
    font-family: "Oswald", sans-serif; font-weight: 600; font-size: 20px;
    letter-spacing: 1px; color: var(--navy); text-transform: uppercase;
  }
  .name-rule { position: absolute; left: 18px; top: 197px; width: 12px; height: 1.5px; background: var(--accent); }
  .contact-list { position: absolute; left: 18px; top: 220px; list-style: none; }
  .contact-item {
    display: flex; align-items: center; gap: 6px; height: 17.5px;
    font-family: "Poppins", sans-serif; font-size: 12px; color: var(--text);
  }
  .contact-item svg { width: 12px; height: 12px; flex: none; }
  .web-domain { color: var(--accent); }
</style>
</head>
<body>
<div class="canvas">

  <section class="card card--front">
    <svg class="card-shapes" viewBox="0 0 501 285" preserveAspectRatio="none" aria-hidden="true">
      <polygon points="175,0 501,0 501,285 458,285" fill="var(--band)"/>
      <polygon points="216,0 501,0 501,270" fill="var(--ink)"/>
      <line x1="196" y1="0" x2="490" y2="285" stroke="#ffffff" stroke-width="0.8"/>
    </svg>
    <div class="brand-name">Keystone<br>Trench Co</div>
    <h1 class="contact-name">Dale Marrick</h1>
    <div class="name-rule"></div>
    <ul class="contact-list">
      <li class="contact-item">
        <svg viewBox="0 0 12 12" fill="none" stroke="var(--accent)" stroke-width="1"><circle cx="6" cy="6" r="5"/><path d="M4 3.5l1 1.5-.6.7a4 4 0 0 0 2 2l.7-.6 1.5 1-.6 1c-2.5 0-4.6-2.1-4.6-4.6z"/></svg>
        555-014-2290
      </li>
      <li class="contact-item">
        <svg viewBox="0 0 12 12" fill="none" stroke="var(--accent)" stroke-width="1"><rect x="1" y="2.5" width="10" height="7"/><path d="M1 2.5l5 4 5-4"/></svg>
        dale@keystonetrenchco.example
      </li>
      <li class="contact-item">
        <svg viewBox="0 0 12 12" fill="none" stroke="var(--accent)" stroke-width="1"><circle cx="6" cy="6" r="5"/><ellipse cx="6" cy="6" rx="2.2" ry="5"/><path d="M1 6h10M2 3.5h8M2 8.5h8"/></svg>
        <span>www.<span class="web-domain">keystonetrenchco</span>.example</span>
      </li>
    </ul>
  </section>

  <section class="card card--back">
    <svg class="card-shapes" viewBox="0 0 501 285" preserveAspectRatio="none" aria-hidden="true">
      <polygon points="288,0 501,0 501,285 2,285" fill="var(--band)"/>
      <polygon points="324,0 501,0 501,285 44,285" fill="var(--ink)"/>
      <line x1="282" y1="0" x2="0" y2="280" stroke="var(--band)" stroke-width="1"/>
    </svg>
    <div class="brand-name brand-name--mark">Keystone<br>Trench Co</div>
    <div class="brand-name brand-name--ghost">Keystone<br>Trench Co</div>
  </section>

</div>
</body>
</html>
```